Bramblewood Card Company Business Cards

We are a trading card store with Glimmorax, sports and other TCG cards, we need a business card design that encompasses a clean cut, modern style with a retro flare. website is bramblewoodcardco.com for reference. Can utilize a comic book era feel or a more modern outdoor feel to utilize the "Pacific Northwest" elements of tress, mountains, etc.

Industry/Entity Type

Trading cards and collectibles

Contact Information for Business Card

business name, email address, phone number, name, owner job title

Font styles to use
Sans Serif

```html
<!DOCTYPE html>
<html lang="en">
<head>
<meta charset="utf-8">
<title>Bramblewood Card Company – Business Cards</title>
<link rel="stylesheet" href="https://fonts.googleapis.com/css2?family=Montserrat:wght@400;500;700;800&display=swap">
<style>
  :root {
    --stage: #2a2a2c;
    --card: #1e1e1f;
    --cyan: #22c1e0;
    --white: #ffffff;
    --divider: #5a5a5c;
  }
  * { box-sizing: border-box; margin: 0; padding: 0; }
  html, body {
    width: 1200px; height: 900px; overflow: hidden;
    background: var(--stage);
    font-family: "Montserrat", sans-serif;
  }
  .sheet {
    width: 1200px; height: 900px;
    display: flex; flex-direction: column; align-items: center; justify-content: center;
    gap: 40px;
  }
  .card {
    position: relative;
    width: 700px; height: 400px;
    background: var(--card);
    border-radius: 22px;
    overflow: hidden;
  }
  .brand {
    position: absolute;
    text-align: center;
    color: var(--white);
    font-weight: 800;
    text-transform: uppercase;
    line-height: 1.1;
  }
  .card--front .brand {
    left: 0; right: 0; top: 50%; transform: translateY(-50%);
    font-size: 40px; letter-spacing: 3px;
  }
  .card--front .brand small { display: block; font-size: 22px; letter-spacing: 8px; }
  .card--back .brand {
    left: 300px; width: 300px; top: 48px;
    font-size: 26px; letter-spacing: 2px;
  }
  .card--back .brand small { display: block; font-size: 14px; letter-spacing: 5px; margin-top: 4px; }

  .person { position: absolute; right: 360px; top: 190px; text-align: right; }
  .person__name { color: var(--cyan); font-weight: 800; font-size: 34px; letter-spacing: 1px; text-transform: uppercase; }
  .person__title { color: var(--white); font-weight: 400; font-size: 19px; margin-top: 2px; }

  .divider { position: absolute; left: 360px; top: 172px; width: 1px; height: 90px; background: var(--divider); }

  .contacts { position: absolute; left: 378px; top: 168px; list-style: none; }
  .contacts li {
    display: flex; align-items: center; gap: 10px;
    color: var(--white); font-size: 17px; font-weight: 400; height: 32px;
    white-space: nowrap;
  }
  .contacts svg { width: 16px; height: 16px; flex: none; }
  .accent { color: var(--cyan); }

  .address-band {
    position: absolute; left: 0; right: 0; top: 300px; height: 44px;
    background: var(--cyan);
    display: flex; align-items: center; padding-left: 110px;
    color: var(--white); font-size: 18px; font-weight: 500; letter-spacing: 0.3px;
    white-space: nowrap;
  }
</style>
</head>
<body>
<main class="sheet">
  <section class="card card--front">
    <div class="brand">Bramblewood<small>Card Company</small></div>
  </section>

  <section class="card card--back">
    <div class="brand">Bramblewood<small>Card Company</small></div>

    <div class="person">
      <p class="person__name">Robin Calder</p>
      <p class="person__title">CEO/Founder</p>
    </div>

    <div class="divider"></div>

    <ul class="contacts">
      <li>
        <svg viewBox="0 0 16 16" aria-hidden="true"><path fill="#22c1e0" d="M3.5 1.5l2.3 0 1 3.2-1.5 1.2a8 8 0 0 0 4.8 4.8l1.2-1.5 3.2 1v2.3c0 .8-.7 1.5-1.5 1.5A12 12 0 0 1 2 3c0-.8.7-1.5 1.5-1.5z"/></svg>
        (555) 318 2764
      </li>
      <li>
        <svg viewBox="0 0 16 16" aria-hidden="true"><rect x="1" y="3" width="14" height="10" rx="1" fill="#22c1e0"/><path d="M1.5 3.8L8 9l6.5-5.2" fill="none" stroke="#1e1e1f" stroke-width="1.3"/></svg>
        info@bramblewoodcardco.com
      </li>
      <li>
        <svg viewBox="0 0 16 16" aria-hidden="true"><g fill="none" stroke="#22c1e0" stroke-width="1.3"><circle cx="8" cy="8" r="6.5"/><ellipse cx="8" cy="8" rx="3" ry="6.5"/><path d="M1.5 8h13M2.5 4.8h11M2.5 11.2h11"/></g></svg>
        <span>www.<span class="accent">bramblewoodcardco</span>.com</span>
      </li>
    </ul>

    <div class="address-band">P.O. Box 3071 Fernhollow Road Cedar Vale AB 6219</div>
  </section>
</main>
</body>
</html>
```